Maple Roster Business Card for recruitment company

We are looking for a Business Card Design that incorporates our personal details and our busines name and logo. We are a specialized search consultancy that recruit Property and Construction professionals.
We would like a business card that stands out and is appealing to the Construction and Property industry as well.

Target Market(s)

people in the construction and property industry

Contact Information for Business Card

Business Name and logo

Font styles to use
Serif

Colors
0094D4
00A9DD
6FCCEA
C7EBF8
E9F6FB

Requirements
Must have
• Business name and logo as well as contact details
Should not have
• No photos of us please

```html
<!DOCTYPE html>
<html lang="en">
<head>
<meta charset="utf-8">
<title>Maple Roster Business Card</title>
<link href="https://fonts.googleapis.com/css2?family=Josefin+Sans:wght@400&family=Oswald:wght@600&family=Montserrat:wght@400&display=swap" rel="stylesheet">
<style>
  :root {
    --backdrop: #1c1d1f;
    --card-deep: #043a4f;
    --card-light: #0d4d63;
    --ink: #ffffff;
  }
  * { margin: 0; padding: 0; box-sizing: border-box; }
  html, body { width: 1200px; height: 900px; overflow: hidden; background: var(--backdrop); }
  .canvas {
    width: 1200px; height: 900px;
    display: flex; flex-direction: column; align-items: center; justify-content: center;
    gap: 34px;
  }
  .card {
    width: 700px; height: 400px;
    background: linear-gradient(135deg, var(--card-deep) 0%, var(--card-light) 55%, var(--card-deep) 100%);
    box-shadow: 0 10px 24px rgba(0,0,0,0.55);
    color: var(--ink);
    position: relative;
  }
  .card-front { display: flex; align-items: center; justify-content: center; }
  .brand-name {
    font-family: "Josefin Sans", sans-serif;
    font-weight: 400;
    font-size: 54px;
    letter-spacing: 5px;
    text-transform: uppercase;
  }
  .card-back {
    display: flex; align-items: center; justify-content: center; gap: 28px;
    padding-right: 20px;
  }
  .identity { text-align: right; }
  .person-name {
    font-family: "Oswald", sans-serif;
    font-weight: 600;
    font-size: 44px;
    line-height: 1;
    text-transform: uppercase;
    letter-spacing: 0.5px;
  }
  .person-role {
    font-family: "Montserrat", sans-serif;
    font-size: 18px;
    letter-spacing: 1px;
    text-transform: uppercase;
    margin-top: 4px;
  }
  .divider { width: 2px; height: 96px; background: var(--ink); }
  .contact-list { list-style: none; font-family: "Montserrat", sans-serif; font-size: 19px; line-height: 1.3; }
  .contact-list li { display: flex; align-items: center; gap: 8px; }
  .contact-list svg { width: 14px; height: 14px; flex: none; }
</style>
</head>
<body>
<main class="canvas">
  <section class="card card-front">
    <h1 class="brand-name">Maple Roster</h1>
  </section>

  <section class="card card-back">
    <div class="identity">
      <p class="person-name">Daniel Hart</p>
      <p class="person-role">Founder</p>
    </div>
    <div class="divider"></div>
    <ul class="contact-list">
      <li>
        <svg viewBox="0 0 16 16" aria-hidden="true"><path d="M4 1 L6.5 4 L5 6 Q7 10 10 11 L12 9.5 L15 12 L13 15 Q5 14 1 3 Z" fill="none" stroke="#fff" stroke-width="1.4"/></svg>
        +64 21 408 2297
      </li>
      <li>
        <svg viewBox="0 0 16 16" aria-hidden="true"><rect x="1" y="3" width="14" height="10" fill="none" stroke="#fff" stroke-width="1.4"/><path d="M1 3 L8 9 L15 3" fill="none" stroke="#fff" stroke-width="1.4"/></svg>
        nora@mapleroster.nz
      </li>
      <li>
        <svg viewBox="0 0 16 16" aria-hidden="true"><circle cx="8" cy="8" r="6.5" fill="none" stroke="#fff" stroke-width="1.3"/><ellipse cx="8" cy="8" rx="3" ry="6.5" fill="none" stroke="#fff" stroke-width="1.1"/><path d="M1.5 8 H14.5" stroke="#fff" stroke-width="1.1"/></svg>
        www.mapleroster.nz
      </li>
      <li>
        <svg viewBox="0 0 16 16" aria-hidden="true"><path d="M8 15 Q2 8 2 6 A6 6 0 0 1 14 6 Q14 8 8 15 Z" fill="#fff"/><circle cx="8" cy="6" r="2.2" fill="#043a4f"/></svg>
        Hamilton, New Zealand
      </li>
    </ul>
  </section>
</main>
</body>
</html>
```